Design a New Business Card for Our Company

We are looking for fresh, unique, and a modern business card that reflects our roots as digital marketing agency focused on SEM.

Industry/Entity Type

Marketing

Contact Information for Business Card

looking for very unique out of the box designs. clean and modern that compliments our logo

Requirements
Must have
• colors should match our logo
• Front should have name, address, email, and phone/fax of the person, phone/fax are the same number
• back should have our url

```html
<!DOCTYPE html>
<html lang="en">
<head>
<meta charset="utf-8">
<title>Nimbus Reach – Business Cards</title>
<link rel="stylesheet" href="https://fonts.googleapis.com/css2?family=Source+Sans+3:wght@400;600;700&display=swap">
<style>
  :root {
    --backdrop: #8f8f8f;
    --paper: #ffffff;
    --brand-blue: #5693d0;
    --brand-grey: #b2b2b2;
    --ink-grey: #8a8a8a;
    --rule-grey: #c4c4c4;
    --white: #ffffff;
  }
  * { box-sizing: border-box; margin: 0; padding: 0; }
  html, body {
    width: 1200px; height: 828px; overflow: hidden;
    background: var(--backdrop);
    font-family: "Source Sans 3", "Myriad Pro", Arial, sans-serif;
  }
  .canvas { position: relative; width: 1200px; height: 828px; }

  .card { position: absolute; overflow: hidden; }

  /* Front card */
  .card--front {
    left: 330px; top: 58px; width: 548px; height: 312px;
    background: var(--paper);
  }
  .brand-lockup {
    position: absolute; left: 32px; top: 136px;
    display: flex; align-items: center; gap: 9px;
  }
  .brand-dot { width: 15px; height: 15px; border-radius: 50%; background: var(--brand-blue); flex: none; }
  .brand-name {
    font-weight: 700; font-size: 30px; line-height: 1;
    color: var(--brand-blue); letter-spacing: -0.5px; white-space: nowrap;
  }
  .divider {
    position: absolute; left: 274px; top: 62px;
    width: 1px; height: 185px; background: var(--rule-grey);
  }
  .contact { position: absolute; left: 293px; top: 62px; color: var(--ink-grey); font-size: 14px; line-height: 19px; }
  .contact__name { color: var(--brand-blue); font-weight: 700; font-size: 17px; line-height: 20px; }
  .contact__role { margin-bottom: 8px; }
  .contact__address { margin-bottom: 10px; }
  .contact__list { list-style: none; }
  .contact__list li { display: flex; align-items: center; gap: 8px; height: 18.7px; }
  .icon { width: 15px; height: 14px; flex: none; }
  .front-stripe {
    position: absolute; left: 0; right: 0; bottom: 18px;
    height: 4px; background: var(--rule-grey);
  }
  .front-band {
    position: absolute; left: 0; right: 0; bottom: 0;
    height: 14px; background: var(--brand-blue);
  }

  /* Back cards */
  .card--back-grey {
    left: 33px; top: 424px; width: 549px; height: 313px;
    background: var(--brand-grey);
  }
  .card--back-blue {
    left: 607px; top: 422px; width: 550px; height: 315px;
    background: var(--brand-blue);
  }
  .emblem-area {
    position: absolute; top: 24px; width: 205px; height: 272px;
    border-radius: 12px;
  }
  .card--back-grey .emblem-area {
    left: 22px;
    background: linear-gradient(160deg, rgba(255,255,255,0.55) 0%, rgba(255,255,255,0.3) 50%, rgba(86,147,208,0.55) 100%);
  }
  .card--back-blue .emblem-area {
    left: 323px;
    background: linear-gradient(200deg, rgba(178,178,178,0.7) 0%, rgba(178,178,178,0.45) 50%, rgba(255,255,255,0.55) 100%);
  }
  .back-lockup {
    position: absolute; display: flex; align-items: center; gap: 8px;
    font-weight: 700; font-size: 34px; line-height: 1; letter-spacing: -0.5px;
    white-space: nowrap; color: var(--white);
  }
  .back-lockup .brand-dot { width: 16px; height: 16px; }
  .back-url { position: absolute; font-size: 14px; color: var(--white); letter-spacing: 0.2px; }

  .card--back-grey .back-lockup { right: 26px; top: 222px; }
  .card--back-grey .back-lockup .brand-dot { background: var(--brand-blue); }
  .card--back-grey .back-url { right: 26px; top: 274px; }

  .card--back-blue .back-lockup { left: 40px; top: 222px; }
  .card--back-blue .back-lockup .brand-dot { background: var(--brand-grey); }
  .card--back-blue .back-url { left: 38px; top: 276px; }
</style>
</head>
<body>
<main class="canvas">

  <section class="card card--front" aria-label="Business card front">
    <div class="brand-lockup">
      <span class="brand-dot"></span>
      <span class="brand-name">Nimbus Reach</span>
    </div>
    <div class="divider"></div>
    <div class="contact">
      <p class="contact__name">Dana Whitford</p>
      <p class="contact__role">Owner</p>
      <p class="contact__address">Nimbus Reach<br>N. 12 Harbor Lane, Suite 200,<br>Tacoma, WA 98401</p>
      <ul class="contact__list">
        <li>
          <svg class="icon" viewBox="0 0 15 14" aria-hidden="true"><rect width="15" height="14" fill="#5693d0"/><path d="M3 5.5c0-1.5 9-1.5 9 0v1h-2.5v-1h-4v1H3z M4.5 7h6l1 4h-8z" fill="#fff"/></svg>
          <span>555.010.2030</span>
        </li>
        <li>
          <svg class="icon" viewBox="0 0 15 14" aria-hidden="true"><rect width="15" height="14" fill="#5693d0"/><rect x="4.5" y="2.5" width="6" height="3.5" fill="#fff"/><rect x="2.5" y="6.5" width="10" height="5" fill="#fff"/></svg>
          <span>555.010.2030</span>
        </li>
        <li>
          <svg class="icon" viewBox="0 0 15 14" aria-hidden="true"><rect width="15" height="14" fill="#5693d0"/><rect x="2.5" y="4" width="10" height="7" fill="#fff"/><path d="M2.5 4l5 4 5-4" fill="none" stroke="#5693d0" stroke-width="1"/></svg>
          <span>hello@nimbusreach.com</span>
        </li>
        <li>
          <svg class="icon" viewBox="0 0 15 14" aria-hidden="true"><rect width="15" height="14" fill="#5693d0"/><circle cx="7.5" cy="7" r="4.5" fill="none" stroke="#fff" stroke-width="1"/><ellipse cx="7.5" cy="7" rx="2" ry="4.5" fill="none" stroke="#fff" stroke-width="1"/><path d="M3 7h9" stroke="#fff" stroke-width="1"/></svg>
          <span>www.nimbusreach.com</span>
        </li>
      </ul>
    </div>
    <div class="front-stripe"></div>
    <div class="front-band"></div>
  </section>

  <section class="card card--back-grey" aria-label="Business card back, grey">
    <div class="emblem-area" role="img" aria-label="Large brand emblem in white and blue"></div>
    <div class="back-lockup">
      <span class="brand-dot"></span>
      <span>Nimbus Reach</span>
    </div>
    <p class="back-url">www.nimbusreach.com</p>
  </section>

  <section class="card card--back-blue" aria-label="Business card back, blue">
    <div class="emblem-area" role="img" aria-label="Large brand emblem in grey and white"></div>
    <div class="back-lockup">
      <span class="brand-dot"></span>
      <span>Nimbus Reach</span>
    </div>
    <p class="back-url">www.nimbusreach.com</p>
  </section>

</main>
</body>
</html>
```